Business Card Design for Marketing Firm

Looking for business card design for higher end marketing firm. Clean but impressionable/trendy. We are a marketing firm that represents manufacturers in the foodservice equipment and supply industry. Our customers are end users such has hotels, restaurants, country clubs, convention centers and casinos as well as distributors of restaurants supplies and equipment, and manufacturers of foodservice equipment and supplies.
Target Market(s)
Hotels, Restaurants, Supply & Equipment Distributors, Foodservice Manufacturers
Industry/Entity Type
Foodservice/Hospitality
Contact Information for Business Card
Name, Title, Contact Number, Email, Website, Social Media, Address
Requirements
Must have
- Clean & Simple but Serious and Impressionable

```html
<!DOCTYPE html>
<html lang="en">
<head>
<meta charset="utf-8">
<title>Meridian Hospitality Reps – Business Card</title>
<link href="https://fonts.googleapis.com/css2?family=Montserrat:wght@500;600;800&display=swap" rel="stylesheet">
<style>
  :root {
    --navy: #2a2a7e;
    --navy-deep: #23236e;
    --white: #ffffff;
    --grey: #bdbdbd;
    --ink: #1c1c2a;
    --stage: #e9e9ee;
  }
  * { margin: 0; padding: 0; box-sizing: border-box; }
  html, body { width: 1200px; height: 960px; overflow: hidden; }
  body {
    background: var(--stage);
    font-family: "Montserrat", sans-serif;
    position: relative;
  }
  .card {
    position: absolute;
    width: 600px;
    height: 343px;
    border-radius: 16px;
    overflow: hidden;
    box-shadow: 0 10px 30px rgba(0,0,0,.18);
  }
  .card-back {
    left: 120px; top: 70px;
    background: linear-gradient(135deg, #35358a, var(--navy-deep));
    display: flex; align-items: center; justify-content: center;
  }
  .card-front {
    left: 480px; top: 540px;
    background: var(--white);
  }
  .brand {
    display: flex; align-items: center; gap: 12px;
    font-weight: 600; letter-spacing: .06em; text-transform: uppercase;
  }
  .brand-dot { width: 14px; height: 14px; border-radius: 50%; background: currentColor; flex: none; }
  .card-back .brand { color: var(--white); font-size: 26px; }
  .card-front .brand {
    position: absolute; left: 38px; top: 150px;
    color: var(--navy); font-size: 16px; width: 240px; line-height: 1.35;
  }
  .divider {
    position: absolute; left: 290px; top: 40px;
    width: 2px; height: 210px; background: var(--navy);
  }
  .contact {
    position: absolute; left: 310px; top: 40px;
    color: var(--ink); font-size: 12.5px; font-weight: 500; line-height: 1.45;
  }
  .contact-name { color: var(--navy); font-weight: 800; font-size: 19px; letter-spacing: .02em; }
  .contact-title { margin-bottom: 8px; }
  .contact-address { margin-bottom: 8px; }
  .contact-row { display: flex; align-items: center; gap: 8px; }
  .contact-row svg { width: 13px; height: 13px; flex: none; }
  .social-dot { width: 13px; height: 13px; border-radius: 50%; background: var(--navy); flex: none; }
  .card-base { position: absolute; left: 0; bottom: 0; width: 600px; height: 90px; }
</style>
</head>
<body>
  <section class="card card-back">
    <div class="brand"><span class="brand-dot"></span>Meridian Hospitality Reps</div>
  </section>

  <section class="card card-front">
    <div class="brand"><span class="brand-dot"></span>Meridian Hospitality Reps</div>
    <div class="divider"></div>
    <div class="contact">
      <div class="contact-name">DANIEL MARSH</div>
      <div class="contact-title">Co-Founder</div>
      <div class="contact-address">P.O. BOX 40-12 NRT-55<br>Linden Ave 14, Fairview</div>
      <div class="contact-row">
        <svg viewBox="0 0 16 16"><path fill="var(--navy)" d="M3 1h3l1 4-2 1a9 9 0 0 0 5 5l1-2 4 1v3a2 2 0 0 1-2 2A13 13 0 0 1 1 3a2 2 0 0 1 2-2z"/></svg>
        555-014-2290
      </div>
      <div class="contact-row">
        <svg viewBox="0 0 16 16"><rect x="1" y="3" width="14" height="10" fill="var(--navy)"/><path d="M1 3l7 6 7-6" stroke="#fff" stroke-width="1.4" fill="none"/></svg>
        info@meridianhospitality.com
      </div>
      <div class="contact-row">
        <svg viewBox="0 0 16 16"><circle cx="8" cy="8" r="7" fill="none" stroke="var(--navy)" stroke-width="1.6"/><path d="M1 8h14M8 1c-3 4-3 10 0 14M8 1c3 4 3 10 0 14" stroke="var(--navy)" stroke-width="1.2" fill="none"/></svg>
        www.meridianhospitality.com
      </div>
      <div class="contact-row">
        <span class="social-dot"></span>
        @meridianhospitality
      </div>
    </div>
    <svg class="card-base" viewBox="0 0 600 90" preserveAspectRatio="none" aria-hidden="true">
      <polygon points="0,72 380,72 362,90 0,90" fill="var(--grey)"/>
      <polygon points="398,56 600,20 600,90 380,90" fill="var(--navy)"/>
    </svg>
  </section>
</body>
</html>
```